The Vantor Codex Book Cover

"The Vantor Codex" is a book I wrote with the slogan "Unlock Performance, Spark Engagement: Master the Art of Building Winning Cultures in Today's Hybrid World". The book is designed around a methodology that's mine and that I attached. I would love to see the graphic of the methodology integrated in the design in a very subtle way. Use colors from the model but the book cover should be catchy, modern and engaging to the eye.
Overall the book is about three key elements towards success:
- (Self) Directions (purpose)
- Human experience (people and psychological safety)
- Maximize engagement
The methodology is a FLOW so flow is something that could be incorporated as well in the concept.
Low design quality
Managers and Teams

```html
<!DOCTYPE html>
<html lang="en">
<head>
<meta charset="utf-8">
<title>The Vantor Codex – Book Cover</title>
<link href="https://fonts.googleapis.com/css2?family=Playfair+Display:wght@900&family=Bebas+Neue&family=Oswald:wght@300;600;700&display=swap" rel="stylesheet">
<style>
  :root {
    --backdrop: #858c99;
    --cover: #ffffff;
    --ink: #111111;
    --blue-deep: #07508f;
    --blue-bright: #1a9ad6;
    --pink: #e8566f;
    --magenta: #b94f86;
    --purple: #5f3f7f;
    --steel: #3f78ad;
    --yellow: #e8c94a;
    --lime: #c9cf58;
    --teal: #7fd6cf;
    --peach: #f0a878;
  }
  * { box-sizing: border-box; margin: 0; padding: 0; }
  html, body { width: 1200px; height: 1122px; overflow: hidden; }
  body {
    background: var(--backdrop);
    display: flex;
    align-items: center;
    justify-content: center;
  }
  .cover {
    width: 740px;
    height: 1040px;
    background: var(--cover);
    display: flex;
    flex-direction: column;
    align-items: center;
    padding: 60px 60px 56px;
  }
  .title-block { width: 100%; text-align: center; }
  .title-top {
    display: flex;
    justify-content: space-between;
    align-items: flex-end;
    width: 100%;
  }
  .title-top__right {
    display: flex;
    flex-direction: column;
    align-items: flex-end;
  }
  .tagline {
    display: inline-block;
    font-family: "Oswald", sans-serif;
    font-weight: 600;
    font-size: 13px;
    letter-spacing: 4px;
    text-transform: uppercase;
    color: var(--ink);
    border-top: 2px solid var(--ink);
    border-bottom: 2px solid var(--ink);
    padding: 3px 10px;
    white-space: nowrap;
  }
  .tagline--left { margin-bottom: 10px; }
  .tagline--right { margin-bottom: 4px; }
  .title {
    font-family: "Playfair Display", serif;
    font-weight: 900;
    line-height: 0.82;
    color: var(--ink);
  }
  .title__the {
    display: block;
    font-size: 78px;
    margin-right: 90px;
  }
  .title__main { display: block; font-size: 140px; margin-top: 4px; }
  .title__accent {
    display: block;
    font-size: 168px;
    background: linear-gradient(180deg, var(--blue-bright), var(--blue-deep));
    -webkit-background-clip: text;
    background-clip: text;
    color: transparent;
    padding-bottom: 12px;
  }
  .subtitle {
    font-family: "Bebas Neue", sans-serif;
    font-size: 34px;
    line-height: 1.05;
    text-align: center;
    color: var(--ink);
    margin-top: 14px;
    letter-spacing: 0.5px;
  }
  .artwork {
    width: 560px;
    height: 280px;
    margin-top: 26px;
    border-radius: 140px;
    background:
      radial-gradient(circle at 28% 50%, var(--magenta) 0%, var(--pink) 25%, var(--peach) 42%, transparent 60%),
      radial-gradient(circle at 72% 50%, var(--lime) 0%, var(--yellow) 20%, var(--teal) 45%, transparent 62%),
      linear-gradient(90deg, var(--purple), var(--steel) 50%, var(--teal));
    opacity: 0.85;
  }
  .author {
    margin-top: auto;
    font-family: "Oswald", sans-serif;
    font-size: 46px;
    letter-spacing: 16px;
    text-transform: uppercase;
    color: var(--ink);
    text-align: center;
    white-space: nowrap;
  }
  .author__first { font-weight: 300; margin-right: 18px; }
  .author__last { font-weight: 700; }
</style>
</head>
<body>
  <main class="cover">
    <header class="title-block">
      <h1 class="title">
        <span class="title-top">
          <span class="tagline tagline--left">Unlock Performance</span>
          <span class="title-top__right">
            <span class="tagline tagline--right">Spark Engagement</span>
            <span class="title__the">The</span>
          </span>
        </span>
        <span class="title__main">Vantor</span>
        <span class="title__accent">Codex</span>
      </h1>
    </header>
    <p class="subtitle">Master the art of building winning<br>cultures in today’s hybrid world</p>
    <div class="artwork" role="img" aria-label="Flow methodology illustration: a colourful segmented wheel with a compass and world map joined in an infinity loop to a ring of people in a hybrid workplace"></div>
    <p class="author"><span class="author__first">Deran</span><span class="author__last">Velthuis</span></p>
  </main>
</body>
</html>
```